NZ First of it's kind solutions directory and marketplace for busy Mums needs a business card design

We need a business card design for our new nationwide business in NZ (long term plans to go global). We provide solutions to the everyday challenges that busy Mums face by connecting them with quality communities and suppliers of carefully selected, relevant products and services. We sell direct via our online marketplace. The final design should communicate our values of inclusivity, quality and smart solutions. Colours should incorporate our logo colour palette of #477077 and #6ba8b2. Our website is at https://www.brightnestmums.example

Target Market(s)

busy Mums, Age 28 – 50, female, income over $100K, location main centres NZ primarily but NZ wide. Is likely juggling work or career with a young family. Probably had hobbies which have fallen by the wayside.
-Wants to succeed in her chosen career without compromising on family life
-to successfully juggle her career without feeling like she is compromising her children
- Is time poor, something always has to give and it’s generally her health (she’ll stay up late, get stressed)
- probably ex corporate or professional career. Has discretional income

Industry/Entity Type

Business

Contact Information for Business Card

Lena Forbisher, Founder, BrightNestMums.example (Strapline Tap; Gather; Sorted), 47 Kowhai Terrace, Ellerslie, Auckland 1051, New Zealand. Mob: 021 483 517 Ph: +64 (0)9 571 4860

Font styles to use
Other font styles liked:
• Raleway, and/or Architects Daughter

Colors
00a990
33b8a4
86cfc6
cfeae6

Requirements
Must have
• the above details, streamline. the logo and colours associated with those logos
Should not have
• foil or metallic colours

```html
<!DOCTYPE html>
<html lang="en">
<head>
<meta charset="utf-8">
<title>BrightNestMums — Business Card</title>
<link rel="stylesheet" href="https://fonts.googleapis.com/css2?family=Arimo:wght@400;700&display=swap">
<style>
  :root {
    --teal-deep: #477077;
    --teal-light: #6ba8b2;
    --card-white: #ffffff;
    --card-mist: #f1f3f3;
    --backdrop: #e6eaea;
    --ink-light: #ffffff;
  }
  * { margin: 0; padding: 0; box-sizing: border-box; }
  html, body {
    width: 1200px;
    height: 900px;
    overflow: hidden;
    background: var(--backdrop);
    font-family: "Arimo", Arial, sans-serif;
  }
  .business-card {
    position: absolute;
    left: 150px;
    top: 172px;
    width: 900px;
    height: 556px;
    background: linear-gradient(90deg, var(--card-white) 40%, var(--card-mist) 100%);
    box-shadow: 0 10px 30px rgba(40, 60, 65, 0.18);
    overflow: hidden;
  }
  .card-panel {
    position: absolute;
    inset: 0;
    width: 900px;
    height: 556px;
  }
  .contact-block {
    position: absolute;
    left: 51px;
    top: 112px;
    color: var(--ink-light);
  }
  .person-name {
    font-size: 31px;
    font-weight: 700;
    letter-spacing: 0.5px;
    line-height: 1.1;
  }
  .person-role {
    font-size: 23px;
    font-weight: 400;
    line-height: 1.2;
  }
  .contact-list {
    list-style: none;
    margin-top: 30px;
  }
  .contact-list li {
    display: flex;
    align-items: center;
    gap: 6px;
    font-size: 24px;
    line-height: 33px;
  }
  .contact-icon {
    width: 20px;
    height: 20px;
    flex: none;
  }
  .postal-address {
    font-style: normal;
    font-size: 24px;
    line-height: 33px;
    margin-top: 17px;
  }
  .brand-mark {
    position: absolute;
    left: 440px;
    top: 418px;
    display: flex;
    align-items: center;
    gap: 12px;
  }
  .brand-dot {
    width: 34px;
    height: 34px;
    border-radius: 50%;
    background: var(--teal-light);
  }
  .brand-name {
    font-size: 44px;
    font-weight: 700;
    color: var(--teal-deep);
    letter-spacing: -0.5px;
  }
</style>
</head>
<body>
  <div class="business-card">
    <svg class="card-panel" viewBox="0 0 900 556" aria-hidden="true">
      <path d="M0 0 H356 C366 60 396 110 436 150 C486 200 486 290 456 360 C426 430 356 480 306 556 H0 Z" fill="var(--teal-light)"/>
      <path d="M0 0 H340 C350 60 380 110 420 150 C470 200 470 290 440 360 C410 430 340 480 290 556 H0 Z" fill="var(--teal-deep)"/>
    </svg>

    <div class="contact-block">
      <h1 class="person-name">LENA FORBISHER</h1>
      <p class="person-role">Founder</p>
      <ul class="contact-list">
        <li>
          <svg class="contact-icon" viewBox="0 0 20 20" aria-hidden="true">
            <path d="M3 8 C3 4 17 4 17 8 L17 10 L13 10 L13 8 L7 8 L7 10 L3 10 Z M5 11 H15 L16 16 H4 Z" fill="currentColor"/>
            <circle cx="10" cy="13.5" r="1.6" fill="var(--teal-deep)"/>
          </svg>
          <span>021 483 517</span>
        </li>
        <li>
          <svg class="contact-icon" viewBox="0 0 20 20" aria-hidden="true">
            <rect x="5" y="2" width="10" height="16" rx="1.5" fill="none" stroke="currentColor" stroke-width="2"/>
            <rect x="8" y="14.5" width="4" height="1.5" fill="currentColor"/>
          </svg>
          <span>+64 (0)9 571 4860</span>
        </li>
        <li>
          <svg class="contact-icon" viewBox="0 0 20 20" aria-hidden="true">
            <circle cx="10" cy="10" r="8" fill="currentColor"/>
            <path d="M10 2 V18 M2 10 H18 M4 6 H16 M4 14 H16" stroke="var(--teal-deep)" stroke-width="1.2" fill="none"/>
          </svg>
          <span>www.BrightNestMums.example</span>
        </li>
      </ul>
      <address class="postal-address">
        47 Kowhai Terrace, Ellerslie<br>
        Auckland 1051, New Zealand
      </address>
    </div>

    <div class="brand-mark">
      <span class="brand-dot"></span>
      <span class="brand-name">BrightNestMums</span>
    </div>
  </div>
</body>
</html>
```